Drone service provider needs a brilliant web design

I need a responsive web design for a new drone service company. Pelham Drone Solutions provides turnkey solutions to capture, process, and deliver actionable aerial data to customers. The design should communicate a professional company that is safe, legal and insured. I included our logo design and business card designs for reference.
*content to be supplied after design selected

Target Market(s)

We serve telecommunications, construction, government, utility infrastructure, insurance and other industries.

Industry/Entity Type

Industrial

Number of Pages Required

5+ page

Colors

Designer to choose colors to be used in the design.

Requirements
Must have
• The design should highlight professional services to include Inspections, Mapping, Consulting and Training. The site should include aerial images and video to compliment the services offered. The landing page must include following sections in order: HOME, SERVICES, ABOUT, DEMO REEL, CLIENTS, CONTACT FORM, and social media buttons (Facebook, LinkedIn, Twitter, YouTube, Instagram). Contact: 615-382-9041 info@pelhamdronesolutions-example.com Smyrna, TN
• Sitemap:
• 6 pages: Home, Inspections, Mapping, Training, Consulting, About
• HOME (Landing Page)
• • Header with logo and tab links (Home, Services, About, Contact)
• • 'CAPTURE. PROCESS. DELIVER.' tagline and 'CONTACT US' button displayed within aerial image of drone over city or construction site
• • Services section with icons, text and read more link to page
• • About section with photo and text with three icons for SAFE. LEGAL. INSURED.
• • Demo reel
• • Clients logos shown scrolling horizontally
• • Contact form
• • Footer with logo, phone, email, social media buttons
• SERVICES (4 different pages)
• • Inspections
• • Mapping
• • Consulting
• • Training
• ABOUT page
• • Company
• • Partners
• • Certifications & Associations
• • Careers
• CONTACT linked to bottom of landing page
• Would you like to receive the newsletter? Yes or No Drop-down list
Nice to have
• Photos of KVR Marlin or Corvex inspecting infrastructure, buildings, construction sites, etc. A photo of one or two pilots in vest and helmet. Free stock photos preferred but would purchase the right photo that's more relevant.
• website references:
• https://www.quillrotor-example.com/
• https://www.brentfieldworks-example.com/services
• https://www.tomaro-example.com/
• http://gantrymetric-example.com/
• http://lumbrook-example.com/
• http://fennotics-example.com/
• https://www.grebe-example.io/
Should not have
• not an aerial photography or videography service business, no blog or newsletter

```html
<!DOCTYPE html>
<html lang="en">
<head>
<meta charset="utf-8">
<title>Mapping – Pelham Drone Solutions</title>
<link href="https://fonts.googleapis.com/css2?family=Open+Sans:wght@400;600;700;800&display=swap" rel="stylesheet">
<style>
:root{
  --brand:#1b93d2;
  --brand-dark:#0f86c6;
  --ink:#222;
  --white:#fff;
  --footer:#282828;
  --muted:#d8d8d8;
}
*{margin:0;padding:0;box-sizing:border-box}
html,body{width:932px;height:1200px;overflow:hidden;background:var(--white)}
body{position:relative;font-family:"Open Sans",sans-serif;color:var(--ink)}
.abs{position:absolute}

/* header */
.site-header{left:0;top:0;width:932px;height:92px;background:var(--brand)}
.header-notch{left:0;top:0;z-index:2}
.main-nav{left:76px;top:37px;display:flex;gap:34px;z-index:3}
.main-nav a{color:var(--white);text-decoration:none;font-size:13px;font-weight:600}
.brand-name{left:350px;top:30px;width:232px;text-align:center;z-index:3;
  font-weight:800;font-size:17px;line-height:20px;color:#1d1d1d;letter-spacing:.5px}
.social{display:flex;gap:8px;z-index:3}
.social span{display:flex;align-items:center;justify-content:center;width:28px;height:28px;border:1.5px solid var(--white);border-radius:50%}
.social.top{left:682px;top:32px}

/* hero */
.hero{left:0;top:93px;width:932px;height:222px;
  background:linear-gradient(180deg,#9aa4ab 0%,#7d8890 45%,#6b7880 70%,#5d6b73 100%)}
.hero-title{left:76px;top:196px;font-size:44px;font-weight:800;color:var(--white);letter-spacing:.5px;z-index:2}

/* content */
.section-title{left:0;top:368px;width:932px;text-align:center;font-size:23px;font-weight:700;color:var(--brand-dark)}
.title-rule{left:445px;top:410px;width:43px;height:2px;background:var(--brand-dark)}
.feature-list{left:178px;top:529px;list-style:none}
.feature-list li{display:flex;align-items:center;height:20px;font-size:12.5px}
.feature-list svg{margin-right:13px}
.divider{left:464px;top:461px;width:4px;height:263px;background:var(--brand-dark);border-radius:2px}
.divider-arrow{left:442px;top:533px}
.feature-photo{left:471px;top:486px;width:283px;height:213px;
  background:linear-gradient(135deg,#7fb0cf 0%,#6a9e7a 55%,#4d8a3a 100%)}
.cta{left:406px;top:775px;width:120px;height:44px;background:var(--brand-dark);color:var(--white);
  font-size:13px;font-weight:700;display:flex;align-items:center;justify-content:center;text-decoration:none}

/* footer */
.site-footer{left:0;top:880px;width:932px;height:320px;background:var(--footer);color:var(--white)}
.footer-brand{left:0;top:956px;width:932px;text-align:center;font-size:18px;font-weight:800;color:var(--white);letter-spacing:.5px}
.contact-row{left:0;top:1033px;width:932px;display:flex;justify-content:center;gap:24px;color:var(--white);font-size:15px}
.contact-row div{display:flex;align-items:center;gap:8px}
.footer-nav{left:245px;top:1095px;display:flex;color:var(--white);font-size:12.5px;font-weight:600}
.footer-nav span.sep{margin:0 42px;color:var(--white);font-weight:400}
.footer-rule{left:76px;top:1140px;width:779px;height:1px;background:var(--muted)}
.copyright{left:76px;top:1161px;font-size:11.5px;color:var(--white)}
.social.bottom{left:711px;top:1158px;gap:6px}
.social.bottom span{width:24px;height:24px}
</style>
</head>
<body>

<header class="abs site-header"></header>
<svg class="abs header-notch" width="932" height="130" viewBox="0 0 932 130" aria-hidden="true">
  <polygon points="350,0 582,0 622,92 310,92" fill="#fff"/>
  <path d="M384 92 A90 90 0 0 0 548 92 Z" fill="#fff"/>
</svg>
<nav class="abs main-nav"><a href="#">HOME</a><a href="#">SERVICES</a><a href="#">ABOUT</a></nav>
<div class="abs brand-name">PELHAM<br>DRONE SOLUTIONS</div>
<div class="abs social top" aria-label="Social media links">
  <span><svg width="12" height="12" viewBox="0 0 12 12"><path d="M4 2h6v6M10 2L3 9" fill="none" stroke="#fff" stroke-width="1.6"/></svg></span>
  <span><svg width="12" height="12" viewBox="0 0 12 12"><path d="M4 2h6v6M10 2L3 9" fill="none" stroke="#fff" stroke-width="1.6"/></svg></span>
  <span><svg width="12" height="12" viewBox="0 0 12 12"><path d="M4 2h6v6M10 2L3 9" fill="none" stroke="#fff" stroke-width="1.6"/></svg></span>
  <span><svg width="12" height="12" viewBox="0 0 12 12"><path d="M4 2h6v6M10 2L3 9" fill="none" stroke="#fff" stroke-width="1.6"/></svg></span>
  <span><svg width="12" height="12" viewBox="0 0 12 12"><path d="M4 2h6v6M10 2L3 9" fill="none" stroke="#fff" stroke-width="1.6"/></svg></span>
</div>

<section class="abs hero" role="img" aria-label="Aerial view of a harbour city with a drone flying over the waterfront"></section>
<svg class="abs" style="left:0;top:93px" width="932" height="222" aria-hidden="true">
  <polyline points="0,145 110,168 380,200 932,222" fill="none" stroke="#1b93d2" stroke-width="3"/>
</svg>
<h1 class="abs hero-title">MAPPING</h1>

<h2 class="abs section-title">MAPPING</h2>
<div class="abs title-rule"></div>

<ul class="abs feature-list">
  <li><svg width="14" height="12" viewBox="0 0 14 12"><path d="M1 5h3v6H1zM4 5l3-4 1 1-1 3h5l-1 6H4z" fill="none" stroke="#1b93d2" stroke-width="1.2"/></svg>Construction Site Progress</li>
  <li><svg width="14" height="12" viewBox="0 0 14 12"><path d="M1 5h3v6H1zM4 5l3-4 1 1-1 3h5l-1 6H4z" fill="none" stroke="#1b93d2" stroke-width="1.2"/></svg>Volumetric Measurements</li>
  <li><svg width="14" height="12" viewBox="0 0 14 12"><path d="M1 5h3v6H1zM4 5l3-4 1 1-1 3h5l-1 6H4z" fill="none" stroke="#1b93d2" stroke-width="1.2"/></svg>2D Orthomosaic Maps</li>
  <li><svg width="14" height="12" viewBox="0 0 14 12"><path d="M1 5h3v6H1zM4 5l3-4 1 1-1 3h5l-1 6H4z" fill="none" stroke="#1b93d2" stroke-width="1.2"/></svg>3D Models</li>
  <li><svg width="14" height="12" viewBox="0 0 14 12"><path d="M1 5h3v6H1zM4 5l3-4 1 1-1 3h5l-1 6H4z" fill="none" stroke="#1b93d2" stroke-width="1.2"/></svg>Point Clouds</li>
  <li><svg width="14" height="12" viewBox="0 0 14 12"><path d="M1 5h3v6H1zM4 5l3-4 1 1-1 3h5l-1 6H4z" fill="none" stroke="#1b93d2" stroke-width="1.2"/></svg>Terrain Models</li>
</ul>

<div class="abs divider"></div>
<svg class="abs divider-arrow" width="24" height="28" aria-hidden="true"><polygon points="24,0 24,28 0,14" fill="#0f86c6"/></svg>
<div class="abs feature-photo" role="img" aria-label="Photo of a mapping drone hovering above a river valley"></div>

<a class="abs cta" href="#">CONTACT US</a>

<footer class="abs site-footer"></footer>
<div class="abs footer-brand">PELHAM DRONE SOLUTIONS</div>
<div class="abs contact-row">
  <div>
    <svg width="28" height="28" viewBox="0 0 28 28"><circle cx="14" cy="14" r="13" fill="none" stroke="#fff" stroke-width="1.4"/><rect x="8" y="10" width="12" height="9" rx="1" fill="none" stroke="#fff" stroke-width="1.3"/><path d="M8 11l6 4 6-4" fill="none" stroke="#fff" stroke-width="1.3"/></svg>
    info@pelhamdronesolutions-example.com
  </div>
  <div>
    <svg width="28" height="28" viewBox="0 0 28 28"><circle cx="14" cy="14" r="13" fill="none" stroke="#fff" stroke-width="1.4"/><path d="M10 8l3 3-1.5 2a8 8 0 0 0 3.5 3.5l2-1.5 3 3-2 2c-5 0-10-5-10-10z" fill="#fff"/></svg>
    615-382-9041
  </div>
</div>
<nav class="abs footer-nav"><span>HOME</span><span class="sep">|</span><span>SERVICES</span><span class="sep">|</span><span>ABOUT</span><span class="sep">|</span><span>CONTACT US</span></nav>
<div class="abs footer-rule"></div>
<p class="abs copyright">Copyright © 2018 Pelham Drone Solutions. All Right Reserved</p>
<div class="abs social bottom" aria-label="Social media links">
  <span><svg width="10" height="10" viewBox="0 0 12 12"><path d="M4 2h6v6M10 2L3 9" fill="none" stroke="#fff" stroke-width="1.6"/></svg></span>
  <span><svg width="10" height="10" viewBox="0 0 12 12"><path d="M4 2h6v6M10 2L3 9" fill="none" stroke="#fff" stroke-width="1.6"/></svg></span>
  <span><svg width="10" height="10" viewBox="0 0 12 12"><path d="M4 2h6v6M10 2L3 9" fill="none" stroke="#fff" stroke-width="1.6"/></svg></span>
  <span><svg width="10" height="10" viewBox="0 0 12 12"><path d="M4 2h6v6M10 2L3 9" fill="none" stroke="#fff" stroke-width="1.6"/></svg></span>
  <span><svg width="10" height="10" viewBox="0 0 12 12"><path d="M4 2h6v6M10 2L3 9" fill="none" stroke="#fff" stroke-width="1.6"/></svg></span>
</div>

</body>
</html>
```